Brochure design for International Beauty Trade Show

I neee a tri-fold company products' brochure to distribute to customers at an international trade show coming soon. We have 4 main product categories- hair and skincare, facial care, Body and bath and massage oil.
The brochure needs to include at least 2 photos of the main products of each category, benefits, call to action and our company contact info ( website and phone number).

Target Market(s)

Educated and high income earners looking for all-natural,pure, 100 organic products for their beauty and personal care needs. Our products cross all racial groups/demographics and suitable for all skin types

Industry/Entity Type

Hair And Beauty

Font styles to use
Serif

Colors

Designer to choose colors to be used in the design.

Requirements
Must have
• The design must stand out as pure and luxury and at the same time be inclusive using our logo design colors- orange and blue. Also, the content must be easy to read and captivating.
• Finally if using women pictures, please include Black, white, Asian and Latina to reflect the fact that our products are suitable for all skin types.
Nice to have
• Design the brochure such that it could be printed as a poster-banner ad.
Should not have
• Cookie cutter designs are not welcome

```html
<!DOCTYPE html>
<html lang="en">
<head>
<meta charset="utf-8">
<title>Velmora Brochure</title>
<link href="https://fonts.googleapis.com/css2?family=Lato:wght@300;400;700&display=swap" rel="stylesheet">
<style>
  :root {
    --blue: #1a8fc8;
    --orange: #f07223;
    --ink: #4a4a4a;
    --paper: #ffffff;
    --backdrop: #eeeeee;
    --photo-a: #6b5a52;
    --photo-b: #2f3a55;
  }
  * { margin: 0; padding: 0; box-sizing: border-box; }
  html, body { width: 1200px; height: 1000px; overflow: hidden; }
  body { background: var(--backdrop); font-family: "Lato", sans-serif; color: var(--ink); position: relative; }

  .brochure { position: absolute; left: 156px; top: 145px; width: 886px; height: 686px; background: var(--paper); overflow: hidden; }
  .bands { position: absolute; left: 0; top: 0; }

  .mission { position: absolute; left: 21px; top: 104px; width: 258px; font-size: 14.5px; font-weight: 300; line-height: 18.5px; text-align: justify; }
  .range-intro { position: absolute; left: 21px; top: 233px; width: 260px; font-size: 14px; font-weight: 300; line-height: 18px; }
  .product-list { position: absolute; left: 26px; top: 274px; list-style: none; font-size: 14.5px; font-weight: 300; }
  .product-list li { height: 26.6px; padding-left: 17px; position: relative; }
  .product-list li::before { content: ""; position: absolute; left: 0; top: 6px; width: 8px; height: 8px; border-radius: 50%; background: var(--blue); }

  .brand { display: flex; align-items: center; gap: 10px; color: var(--orange); font-weight: 700; }
  .brand-dot { border-radius: 50%; background: var(--blue); flex: none; }
  .brand--middle { position: absolute; left: 380px; top: 348px; width: 122px; justify-content: center; font-size: 26px; }
  .brand--middle .brand-dot { width: 14px; height: 14px; }
  .brand--cover { position: absolute; left: 587px; top: 122px; width: 299px; justify-content: center; font-size: 40px; }
  .brand--cover .brand-dot { width: 22px; height: 22px; }

  .order { position: absolute; left: 300px; top: 476px; width: 282px; text-align: center; }
  .order-heading { color: var(--blue); font-weight: 700; font-size: 19px; letter-spacing: 0.5px; }
  .order-web, .order-mail { font-size: 19px; font-weight: 400; letter-spacing: 0.4px; line-height: 24px; }
  .order-web { margin-top: 14px; }
  .order-phone { color: var(--orange); font-size: 33px; font-weight: 400; letter-spacing: 1px; margin-top: 8px; }

  .tagline { position: absolute; left: 587px; top: 275px; width: 299px; text-align: center; }
  .tagline-main { color: var(--blue); font-weight: 700; font-size: 22px; }
  .tagline-sub { color: var(--orange); font-size: 21px; font-weight: 400; margin-top: 2px; }

  .cover-photo { position: absolute; left: 587px; top: 410px; width: 299px; height: 276px; background: linear-gradient(135deg, var(--photo-a), #8a7064 45%, var(--photo-b)); }
</style>
</head>
<body>
  <main class="brochure">
    <svg class="bands" width="886" height="686" viewBox="0 0 886 686" aria-hidden="true">
      <polygon points="0,0 587,0 587,105 0,23" fill="var(--blue)"/>
      <polygon points="0,585 587,663 587,686 0,686" fill="var(--orange)"/>
    </svg>

    <section class="panel-inside">
      <p class="mission">Our mission is to satisfy our customers by supplying them with pure, natural and 100% organic products, which make them more attractive and solve the most common skin and hair problems.</p>
      <p class="range-intro">Over 20 luxury Products to choose from including:</p>
      <ul class="product-list">
        <li>Argan oil</li>
        <li>Moroccan Beldi Soaps</li>
        <li>Prickly Pear seed oil</li>
        <li>Shea Butter</li>
        <li>Carrot oil</li>
        <li>Green Clay Mask</li>
        <li>Castor oil</li>
        <li>Stretch marks/vergeture oil</li>
        <li>Massage oil</li>
        <li>Black Soaps</li>
      </ul>
    </section>

    <section class="panel-back">
      <div class="brand brand--middle"><span class="brand-dot"></span>Velmora</div>
      <div class="order">
        <p class="order-heading">ORDER NOW AT:</p>
        <p class="order-web">www.velmora.com</p>
        <p class="order-mail">info@velmora.com</p>
        <p class="order-phone">(800) 555-0147</p>
      </div>
    </section>

    <section class="panel-cover">
      <div class="brand brand--cover"><span class="brand-dot"></span>Velmora</div>
      <div class="tagline">
        <p class="tagline-main">NATURAL SOLUTIONS</p>
        <p class="tagline-sub">to Forever Beauty</p>
      </div>
      <div class="cover-photo" role="img" aria-label="Photo of five smiling women of diverse backgrounds standing close together"></div>
    </section>
  </main>
</body>
</html>
```